Financial Services Consultant needs a business card

We need a business card for a new consulting company based in Melbourne called
"Quelbrook Insights". Tagline is Assess, Track, Improve
We would like to see business card designs that are in line with the minimal style of the website www.quelbrook-insights.example
The font I have used on the website is Proxima Nova and would like the same or similar font used on the business card with a minimal design in line with the website Two sided with "QUELBROOK INSIGHTS" ASSESS, TRACK, IMPROVE on one side and name, title and contact details on the otther
Updates

Hi All, thanks for your submissions, much appreciated.

I have recently added some colour to my webiste, it is hex #3a7b74 for those that wish to use it
Thanks

Hi all

thanks very much for your design submissions I am very impressed and they are much appreciated.

Interms of general feedback please find below;

Colour: I am trying to stick to a minimal design and colour scheme for my website which is still under construction, up to 3 colours( www.quelbrook-insights.example) it is currently black and white with a small amount of blue/green but I am open to suggestion/interpretations for a consulting company.

Card: I dont mind if it has rounded edges or straight, I was thinking about using a letterpress card if possible

Detail: the detail on the card will include; Name, Title, Mobile, Personal Email, Business Email,Web,Business Address

Once again thanks for submissions

Industry/Entity Type

Business

```html
<!DOCTYPE html>
<html lang="en">
<head>
<meta charset="utf-8">
<title>Quelbrook Insights — Business Card</title>
<link rel="stylesheet" href="https://fonts.googleapis.com/css2?family=Montserrat:wght@400;500;700&display=swap">
<style>
  :root {
    --backdrop: #2b2b2b;
    --card: #f7f7f7;
    --ink: #1c1c1c;
    --ink-soft: #3a3a3a;
  }
  html, body {
    margin: 0;
    padding: 0;
    width: 1200px;
    height: 900px;
    overflow: hidden;
    background: var(--backdrop);
  }
  .canvas {
    width: 1200px;
    height: 900px;
    display: flex;
    flex-direction: column;
    align-items: center;
    justify-content: center;
    gap: 40px;
    font-family: "Montserrat", sans-serif;
    color: var(--ink);
  }
  .card {
    position: relative;
    width: 700px;
    height: 400px;
    background: var(--card);
    box-sizing: border-box;
  }
  /* Front */
  .card--front {
    display: flex;
    flex-direction: column;
    align-items: center;
    justify-content: center;
  }
  .brand-name {
    margin: 0;
    font-size: 34px;
    font-weight: 700;
    letter-spacing: 0.14em;
    padding-left: 0.14em;
  }
  .tagline {
    margin: 14px 0 0;
    font-size: 13px;
    font-weight: 500;
    letter-spacing: 0.42em;
    padding-left: 0.42em;
    color: var(--ink-soft);
  }
  /* Back */
  .person {
    position: absolute;
    top: 120px;
    left: 250px;
    text-align: center;
  }
  .person-name {
    margin: 0;
    font-size: 22px;
    font-weight: 700;
    letter-spacing: 0.2em;
  }
  .person-title {
    margin: 4px 0 0;
    font-size: 13px;
    font-weight: 500;
    color: var(--ink-soft);
  }
  .address {
    position: absolute;
    top: 190px;
    right: 50px;
    text-align: right;
    font-style: normal;
    font-size: 15px;
    font-weight: 500;
    line-height: 1.45;
  }
  .contact {
    position: absolute;
    left: 55px;
    bottom: 45px;
    margin: 0;
    padding: 0;
    list-style: none;
    font-size: 15px;
    font-weight: 500;
    line-height: 1.5;
  }
</style>
</head>
<body>
  <main class="canvas">
    <section class="card card--front" aria-label="Card front">
      <h1 class="brand-name">QUELBROOK INSIGHTS</h1>
      <p class="tagline">ASSESS, TRACK, IMPROVE</p>
    </section>

    <section class="card card--back" aria-label="Card back">
      <div class="person">
        <h2 class="person-name">ELLIOT VARNHAM</h2>
        <p class="person-title">managing director</p>
      </div>
      <address class="address">
        48 Larkspur Lane<br>
        Carlton, Victoria 3053<br>
        www.quelbrook-insights.example
      </address>
      <ul class="contact">
        <li>03 9410 27 65</li>
        <li>0412 386 905</li>
        <li>info@quelbrook-insights.example</li>
      </ul>
    </section>
  </main>
</body>
</html>
```